Business card design for Virtual Assistance company

I need a business card designed for my virtual assistance company. We are a small company who services primarily C-level executive clients. The card needs to be double sided with the following contact information on the back:
Melissa Thornbury
Owner/CEO
info@rkpadvisory.net
www.rkpadvisory.net
555.302.9817

The front side should just have the company name incorporated: "RKP Advisory" and "virtual assistance"

The card should be simplistic, but eye catching and should speak to high level executives. Our primary focus areas consist of executive assistance and government contracting.

Target Market(s)

CEOs and executives

Contact Information for Business Card

see project description. phone, email, website.

Colors

Designer to choose only greyscale colors for use in the design.

```html
<!DOCTYPE html>
<html lang="en">
<head>
<meta charset="utf-8">
<title>RKP Advisory – Business Card</title>
<link rel="stylesheet" href="https://fonts.googleapis.com/css2?family=Cinzel:wght@500&family=Poppins:wght@400&display=swap">
<style>
  :root {
    --backdrop: #2d2d2d;
    --card: #050505;
    --metal: #c4c4c4;
    --metal-light: #f0f0f0;
    --metal-dark: #7c7c7c;
  }
  * { margin: 0; padding: 0; box-sizing: border-box; }
  html, body {
    width: 1200px;
    height: 1015px;
    overflow: hidden;
    background: var(--backdrop);
  }
  .canvas {
    width: 1200px;
    height: 1015px;
    display: flex;
    flex-direction: column;
    align-items: center;
    justify-content: center;
    gap: 44px;
  }
  .card {
    position: relative;
    width: 760px;
    height: 434px;
    background: var(--card);
    box-shadow: 0 14px 30px rgba(0,0,0,0.45);
    color: var(--metal);
    overflow: hidden;
  }
  .card__stripe {
    position: absolute;
    left: 0;
    right: 0;
    bottom: 14px;
    height: 7px;
    background: linear-gradient(90deg, var(--metal-dark), var(--metal-light) 35%, var(--metal) 60%, var(--metal-light) 85%, var(--metal-dark));
  }

  /* Front */
  .front__brand {
    position: absolute;
    inset: 0 0 40px 0;
    display: flex;
    flex-direction: column;
    align-items: center;
    justify-content: center;
  }
  .brand-name {
    font-family: "Cinzel", serif;
    font-weight: 500;
    font-size: 62px;
    letter-spacing: 4px;
    color: var(--metal);
    line-height: 1;
  }
  .tagline {
    display: flex;
    align-items: center;
    gap: 14px;
    margin-top: 16px;
    font-family: "Poppins", sans-serif;
    font-size: 15px;
    letter-spacing: 5px;
    text-transform: uppercase;
    color: var(--metal);
  }
  .tagline__rule {
    width: 44px;
    height: 2px;
    background: var(--metal);
  }

  /* Back */
  .back__holder {
    position: absolute;
    left: 52px;
    top: 92px;
  }
  .holder-name {
    font-family: "Cinzel", serif;
    font-weight: 500;
    font-size: 24px;
    letter-spacing: 1px;
    text-transform: uppercase;
    line-height: 1.1;
    white-space: nowrap;
  }
  .holder-title {
    font-family: "Poppins", sans-serif;
    font-size: 19px;
    line-height: 1.3;
  }
  .back__brand {
    position: absolute;
    right: 46px;
    top: 58px;
    font-family: "Cinzel", serif;
    font-weight: 500;
    font-size: 38px;
    letter-spacing: 3px;
    line-height: 1;
    white-space: nowrap;
    color: var(--metal);
  }
  .contact-list {
    position: absolute;
    left: 52px;
    bottom: 58px;
    list-style: none;
    font-family: "Poppins", sans-serif;
    font-size: 20px;
    line-height: 1.45;
  }
  .contact-list__item {
    display: flex;
    align-items: center;
    gap: 12px;
  }
  .contact-list__icon {
    width: 20px;
    height: 20px;
    flex: none;
  }
</style>
</head>
<body>
<main class="canvas">

  <section class="card card--front" aria-label="Card front">
    <div class="front__brand">
      <div class="brand-name">RKP ADVISORY</div>
      <div class="tagline">
        <span class="tagline__rule"></span>
        <span>Virtual Assistance</span>
        <span class="tagline__rule"></span>
      </div>
    </div>
    <div class="card__stripe"></div>
  </section>

  <section class="card card--back" aria-label="Card back">
    <div class="back__holder">
      <div class="holder-name">Melissa Thornbury</div>
      <div class="holder-title">Owner/CEO</div>
    </div>

    <div class="back__brand">RKP ADVISORY</div>

    <ul class="contact-list">
      <li class="contact-list__item">
        <svg class="contact-list__icon" viewBox="0 0 24 24" fill="var(--metal)" aria-hidden="true">
          <path d="M6.6 10.8a15.1 15.1 0 0 0 6.6 6.6l2.2-2.2a1 1 0 0 1 1-.25 11.4 11.4 0 0 0 3.6.57 1 1 0 0 1 1 1V20a1 1 0 0 1-1 1A17 17 0 0 1 3 4a1 1 0 0 1 1-1h3.5a1 1 0 0 1 1 1c0 1.250.2 2.450.57 3.6a1 1 0 0 1-.25 1z"/>
        </svg>
        <span>555.302.9817</span>
      </li>
      <li class="contact-list__item">
        <svg class="contact-list__icon" viewBox="0 0 24 24" fill="var(--metal)" aria-hidden="true">
          <path d="M2 5h20v14H2z M4 7v.4l8 5.2 8-5.2V7z" fill-rule="evenodd"/>
        </svg>
        <span>info@rkpadvisory.net</span>
      </li>
      <li class="contact-list__item">
        <svg class="contact-list__icon" viewBox="0 0 24 24" fill="none" stroke="var(--metal)" stroke-width="1.8" aria-hidden="true">
          <circle cx="12" cy="12" r="9.5"/>
          <ellipse cx="12" cy="12" rx="4" ry="9.5"/>
          <path d="M2.5 12h19M4 7h16M4 17h16"/>
        </svg>
        <span>www.rkpadvisory.net</span>
      </li>
    </ul>

    <div class="card__stripe"></div>
  </section>

</main>
</body>
</html>
```